Moravel Aesthetic Doctor

I require an elegant, luxurious looking business card for my aesthetic business. I am a doctor and that will set me aside from competitors. I am planning to provide home and spa based treatments to clients with high expectations. I have attached my logo.

```html
<!DOCTYPE html>
<html lang="en">
<head>
<meta charset="utf-8">
<title>Moravel Aesthetic Doctor — Business Card</title>
<link rel="stylesheet" href="https://fonts.googleapis.com/css2?family=Arimo:wght@400;700&display=swap">
<style>
  :root {
    --stage: #262628;
    --card-dark: #1c1b20;
    --card-light: #ffffff;
    --sky: #7ecbea;
    --blue: #3aa9e0;
    --grey: #9a9a9e;
    --grey-dark: #8a8a8e;
    --white: #ffffff;
    --rule: #b5b5b8;
  }
  * { box-sizing: border-box; margin: 0; padding: 0; }
  html, body { width: 1200px; height: 900px; overflow: hidden; }
  body {
    background: var(--stage);
    font-family: "Arimo", Arial, sans-serif;
    position: relative;
  }
  .card {
    position: absolute;
    left: 280px;
    width: 640px;
    height: 366px;
    overflow: hidden;
  }
  .card--front { top: 60px; background: var(--card-dark); }
  .card--back  { top: 474px; background: var(--card-light); }

  /* Brand lockup */
  .brand { position: absolute; display: flex; align-items: center; gap: 22px; white-space: nowrap; }
  .brand__mark {
    flex: none;
    width: 96px; height: 96px; border-radius: 50%;
    border: 3px solid var(--grey);
    background: radial-gradient(circle at 40% 45%, #8fd3f2, #2f8fcf);
  }
  .brand__name { font-weight: 400; color: var(--grey); line-height: 1; }
  .brand__name .big { display: block; font-size: 54px; letter-spacing: 4px; }
  .brand__name .small { display: block; font-size: 21px; letter-spacing: 2px; margin-top: 6px; }

  .card--front .brand { left: 150px; top: 50px; }
  .card--front .brand__name { color: #c9c9cc; }

  .band {
    position: absolute; left: 0; right: 0; top: 180px; height: 38px;
    background: var(--sky);
    color: var(--white);
    font-size: 17px; letter-spacing: 0.5px;
    display: flex; align-items: center; justify-content: center;
  }
  .services {
    position: absolute; left: 0; right: 0; top: 240px;
    color: var(--white); text-align: center;
    font-size: 17px; line-height: 28px;
    list-style: none;
  }
  .services .dot {
    display: inline-block; width: 8px; height: 8px; border-radius: 50%;
    background: var(--sky); margin: 0 10px; vertical-align: middle;
  }

  /* Back */
  .card--back .brand { left: 36px; top: 150px; gap: 14px; }
  .card--back .brand__mark { width: 72px; height: 72px; }
  .card--back .brand__name .big { font-size: 36px; letter-spacing: 2px; }
  .card--back .brand__name .small { font-size: 14px; letter-spacing: 1.5px; margin-top: 5px; }
  .divider {
    position: absolute; left: 334px; top: 70px; width: 1px; height: 210px;
    background: var(--rule);
  }
  .contact { position: absolute; left: 356px; top: 78px; right: 16px; }
  .contact__name { font-weight: 700; font-size: 24px; color: var(--grey-dark); white-space: nowrap; }
  .contact__post { font-weight: 400; font-size: 13px; color: var(--blue); margin-left: 4px; }
  .contact__cred { color: var(--blue); font-size: 17px; line-height: 23px; margin-top: 6px; }
  .contact__list { list-style: none; margin-top: 22px; }
  .contact__list li {
    display: flex; align-items: center; gap: 12px;
    font-size: 17px; color: var(--grey-dark); line-height: 29px; white-space: nowrap;
  }
  .contact__list svg { width: 17px; height: 17px; flex: none; }
</style>
</head>
<body>

<section class="card card--front">
  <div class="brand">
    <div class="brand__mark" role="img" aria-label="Brand emblem: stylised profile with flowing blue hair"></div>
    <div class="brand__name"><span class="big">MORAVEL</span><span class="small">AESTHETIC DOCTOR</span></div>
  </div>
  <div class="band">HOME AND SPA BASED TREATMENTS</div>
  <ul class="services">
    <li>Dermal injectables<span class="dot"></span>Plasma facials<span class="dot"></span>Microneedling</li>
    <li>Skin boosters<span class="dot"></span>Excessive sweating</li>
    <li>Home and Spa Based Treatments</li>
  </ul>
</section>

<section class="card card--back">
  <div class="brand">
    <div class="brand__mark" role="img" aria-label="Brand emblem: stylised profile with flowing blue hair"></div>
    <div class="brand__name"><span class="big">MORAVEL</span><span class="small">AESTHETIC DOCTOR</span></div>
  </div>
  <div class="divider"></div>
  <div class="contact">
    <p class="contact__name">Dr Elin Marsh<span class="contact__post">MRCPCH MD</span></p>
    <p class="contact__cred">Australasian Diploma of<br>Aesthetic Medicine</p>
    <ul class="contact__list">
      <li>
        <svg viewBox="0 0 24 24" aria-hidden="true"><path fill="#3aa9e0" d="M6.6 10.8a15.1 15.1 0 0 0 6.6 6.6l2.2-2.2a1 1 0 0 1 1-.25 11.4 11.4 0 0 0 3.6.6 1 1 0 0 1 1 1V20a1 1 0 0 1-1 1A17 17 0 0 1 3 4a1 1 0 0 1 1-1h3.5a1 1 0 0 1 1 1c0 1.25.2 2.45.6 3.6a1 1 0 0 1-.25 1z"/></svg>
        0800 555 014
      </li>
      <li>
        <svg viewBox="0 0 24 24" aria-hidden="true"><rect x="2" y="5" width="20" height="14" fill="#3aa9e0"/><path d="M2 5l10 8 10-8" fill="none" stroke="#fff" stroke-width="1.6"/></svg>
        elin@moravel.co.nz
      </li>
      <li>
        <svg viewBox="0 0 24 24" aria-hidden="true"><g fill="none" stroke="#3aa9e0" stroke-width="1.8"><circle cx="12" cy="12" r="9"/><ellipse cx="12" cy="12" rx="4" ry="9"/><path d="M3 12h18M5 7h14M5 17h14"/></g></svg>
        www.moravel.co.nz
      </li>
    </ul>
  </div>
</section>

</body>
</html>
```